2020 Teamwear Price List

Price list of our popular teamwear items that we wholesale to clubs and schools.
looking to create a price list with images, images can be obtained from our website:
www.corvelathletichub.com.au
price list does not have to have lots of details about each product, just a from price. with minimum order etc.
and we can email or post to our clients, so it can be A4 pages/booklet style.
i can also provide images after i choose the design layout we like, so you can just use generic images for now if required.
Updates

Target Market(s)

Clubs and Schools

Font styles to use
Sans Serif

Colors

Designer to choose colors to be used in the design.

Requirements
Must have
• Photo or generated image for each product.
Nice to have
• simple format , easy to read , and easy to update from time to time

```html
<!DOCTYPE html>
<html lang="en">
<head>
<meta charset="utf-8">
<title>Teamwear Price List</title>
<link rel="stylesheet" href="https://fonts.googleapis.com/css2?family=Lato:wght@400;700&family=Archivo:ital,wght@1,900&display=swap">
<style>
:root{
  --red:#d71920;
  --black:#0d0d0d;
  --white:#ffffff;
  --grey-band:#d4d4d4;
  --backdrop:#8c909e;
  --garment:#1a1a1a;
  --text:#222222;
}
*{box-sizing:border-box;margin:0;padding:0}
html,body{width:1200px;height:1200px;overflow:hidden;background:var(--backdrop)}
body{font-family:"Lato",sans-serif;position:relative}
.sheet{position:absolute;left:207px;top:44px;width:786px;height:1112px;background:var(--white);overflow:hidden;box-shadow:0 10px 30px rgba(0,0,0,.35)}
.masthead{position:absolute;left:0;top:0;width:786px;height:118px;background:var(--black)}
.masthead-red{position:absolute;left:0;top:0}
.brand{position:absolute;left:40px;top:40px;display:flex;align-items:center;gap:10px;color:var(--black);font-weight:700;font-size:36px;letter-spacing:1px}
.brand-dot{width:20px;height:20px;border-radius:50%;background:var(--black)}
.contact{position:absolute;left:470px;top:20px;color:var(--white);font-size:15px;line-height:19px}
.contact p{display:flex;align-items:center;gap:8px}
.contact .lead{margin-left:25px}
.contact svg{flex:none}
.title-band{position:absolute;left:0;top:120px;width:786px;height:44px}
.title{position:absolute;left:80px;top:120px;height:44px;line-height:47px;font-family:"Archivo",sans-serif;font-style:italic;font-weight:900;font-size:46px;color:var(--white);letter-spacing:1px;white-space:nowrap}
.terms{position:absolute;left:0;top:164px;width:786px;height:49px;background:var(--grey-band);text-align:center;font-size:13.5px;line-height:17px;padding-top:7px;color:var(--text)}
.section-head{position:absolute;left:26px;top:238px;display:flex;align-items:center;gap:6px;font-family:"Archivo",sans-serif;font-style:italic;font-weight:900;font-size:32px;color:var(--red)}
.section-rule{position:absolute;left:0;top:280px;width:280px;height:3px;background:var(--red)}
.hero{position:absolute;left:453px;top:232px;width:333px;height:304px;background:radial-gradient(ellipse at 45% 55%,#8a8a8a 0%,#c4c4c4 40%,#efefef 70%,#ffffff 90%)}
.card{position:absolute;width:174px;border-left:4px solid var(--red);border-right:4px solid var(--red);border-image:linear-gradient(to bottom,var(--red) 0%,var(--red) 60%,rgba(215,25,32,0) 100%) 1}
.card-head{background:var(--red);color:var(--white);text-align:center;font-size:14.5px;line-height:17.5px;padding-top:4px;margin:0 -4px;white-space:nowrap}
.card-head.tight{font-size:13.5px;letter-spacing:-.2px}
.card-img{margin:14px auto 0;width:90px;height:108px;background:linear-gradient(180deg,#3a3a3a,var(--garment));border-radius:10px}
.card-img.hood{width:76px;height:118px;border-radius:30px 30px 6px 6px}
.price{text-align:center;color:var(--red);font-weight:700;font-size:21px;margin-top:18px}
.hood + .price{margin-top:8px}
.footer-rule{position:absolute;left:0;top:1044px;width:786px;height:4px;background:var(--black)}
.footer{position:absolute;left:0;top:1056px;width:786px;height:56px;background:linear-gradient(90deg,var(--black) 0%,#7a0e12 40%,var(--red) 100%);color:var(--white);text-align:center;font-size:21px;line-height:56px}
</style>
</head>
<body>
<main class="sheet">
  <header class="masthead">
    <svg class="masthead-red" width="786" height="118"><polygon points="0,0 397,0 323,118 0,118" fill="var(--red)"/></svg>
    <div class="brand"><span class="brand-dot"></span>VENDRASK</div>
    <div class="contact">
      <p class="lead">Please contact us for an official quote:</p>
      <p><svg width="16" height="16" viewBox="0 0 16 16"><circle cx="8" cy="8" r="8" fill="var(--red)"/><path d="M5 4l2 2-1 1c.6 1.2 1.6 2.2 2.8 2.8l1-1 2 2-1.2 1.2C7.6 12 4 8.4 3.8 5.2z" fill="#fff"/></svg>03 5550 1274</p>
      <p><svg width="16" height="16" viewBox="0 0 16 16"><circle cx="8" cy="8" r="8" fill="var(--red)"/><rect x="4" y="5" width="8" height="6" fill="none" stroke="#fff"/><path d="M4 5l4 3 4-3" fill="none" stroke="#fff"/></svg>sam@corvelathletichub.com.au</p>
      <p><svg width="16" height="16" viewBox="0 0 16 16"><circle cx="8" cy="8" r="8" fill="var(--red)"/><circle cx="8" cy="8" r="4.5" fill="none" stroke="#fff"/><path d="M3.5 8h9M8 3.5c-2 2.5-2 6.5 0 9M8 3.5c2 2.5 2 6.5 0 9" fill="none" stroke="#fff" stroke-width=".8"/></svg>www.corvelathletichub.com.au</p>
    </div>
  </header>

  <svg class="title-band" width="786" height="44"><rect width="786" height="44" fill="var(--red)"/><polygon points="0,0 395,0 380,44 0,44" fill="var(--black)"/></svg>
  <h1 class="title">TEAMWEAR PRICE LIST</h1>
  <p class="terms">Prices shown below exclude GST, Custom Clothing is based on order of 20 + units,<br>smaller order quantities are available on request</p>

  <h2 class="section-head"><svg width="24" height="26"><polygon points="0,0 24,13 0,26" fill="var(--red)"/></svg>GENERAL</h2>
  <div class="section-rule"></div>

  <div class="hero" role="img" aria-label="Athlete in a grey training shirt holding dumbbells, with a grey paint splash behind"></div>

  <article class="card" style="left:25px;top:301px;height:219px"><div class="card-head" style="height:44px">1 CLUB POLOS<br>with 1 logo embroidered</div><div class="card-img" role="img" aria-label="Black polo shirt"></div><p class="price">$21</p></article>
  <article class="card" style="left:213px;top:301px;height:219px"><div class="card-head" style="height:44px">CLUB HOODIE<br>with 1 logo embroidered</div><div class="card-img hood" role="img" aria-label="Black hoodie"></div><p class="price">$29</p></article>

  <article class="card" style="left:25px;top:549px;height:223px"><div class="card-head" style="height:44px">SUBLIMATED POLOS<br>Unlimited logos</div><div class="card-img" role="img" aria-label="Black polo shirt"></div><p class="price">$36</p></article>
  <article class="card" style="left:213px;top:549px;height:223px"><div class="card-head" style="height:44px">SUBLIMATED T SHIRTS<br>Unlimited logos</div><div class="card-img" role="img" aria-label="Black t-shirt"></div><p class="price">$35</p></article>
  <article class="card" style="left:399px;top:549px;height:223px"><div class="card-head" style="height:44px">SUBLIMATED SINGLETS<br>Unlimited logos</div><div class="card-img" role="img" aria-label="Black singlet"></div><p class="price">$31</p></article>
  <article class="card" style="left:586px;top:549px;height:223px"><div class="card-head" style="height:44px">SUBLIMATED HOODIES<br>Unlimited logos</div><div class="card-img hood" role="img" aria-label="Black hoodie"></div><p class="price">$59</p></article>

  <article class="card" style="left:25px;top:800px;height:232px"><div class="card-head" style="height:58px">WALK OUT SHORTS<br>with 1 logo embroidered</div><div class="card-img" role="img" aria-label="Black shorts"></div><p class="price">$36</p></article>
  <article class="card" style="left:213px;top:800px;height:232px"><div class="card-head tight" style="height:58px">MICROFIBRE TRACK PANTS<br>with 1 logo embroidered</div><div class="card-img" role="img" aria-label="Black track pants"></div><p class="price">$35</p></article>
  <article class="card" style="left:399px;top:800px;height:232px"><div class="card-head" style="height:58px">TAPPERED LEG FLEECY<br>TRACK PANTS<br>with 1 logo embroidered</div><div class="card-img" role="img" aria-label="Black fleece track pants"></div><p class="price">$31</p></article>
  <article class="card" style="left:586px;top:800px;height:232px"><div class="card-head" style="height:58px">10 SUPPORTER<br>SOFTSHELL JACKETS<br>with 1 logo embroidered</div><div class="card-img hood" role="img" aria-label="Black softshell jacket"></div><p class="price">$59</p></article>

  <div class="footer-rule"></div>
  <footer class="footer">www.corvelathletichub.com.au</footer>
</main>
</body>
</html>
```